Informational Site for Advanced Chemistry R&D

The company develops oxidation chemistry for air, water, fuel pollution controls. The site has been prototyped at www.velquaresearch.example. Take a look. Now, the task is to design it for eye-catching beauty with use of color, on-page scroll-driven color transition and parallax effects. Should capture the themes: high technology, wow it's beautiful, modern, uncluttered, clean urban environment.

Target Market(s)

China Environmentally Conscious Government and Industry,

Industry/Entity Type

It Company

Number of Pages Required

3 page

Font styles to use
Sans Serif

Requirements
Must have
• Parallax effects, desktop compatible, Rich, Modern, Simple, Graphic
Nice to have
• Mobile Phone Compatible
Should not have
• Flash, or anything that is slow to load or requires high bandwidth

```html
<!DOCTYPE html>
<html lang="en">
<head>
<meta charset="utf-8">
<title>Velqua Sciences — Advanced Oxidation Science</title>
<link href="https://fonts.googleapis.com/css2?family=Roboto:wght@300;400;500;700&display=swap" rel="stylesheet">
<style>
:root{
  --teal:#25b5ad;
  --teal-dark:#1c9a93;
  --blue:#1d6fae;
  --blue-deep:#155a93;
  --ink:#333333;
  --muted:#6b6b6b;
  --line:#e3e3e3;
  --light:#f4f5f6;
  --footer:#2f3133;
  --footer-deep:#232425;
  --white:#ffffff;
}
*{box-sizing:border-box;margin:0;padding:0}
html,body{width:1200px;height:3904px;overflow:hidden}
body{font-family:"Roboto",Arial,sans-serif;color:var(--ink);background:var(--white);position:relative}
a{color:inherit;text-decoration:none}
.wordmark{font-weight:700;color:var(--blue);font-size:22px;display:flex;align-items:center;gap:8px}
.wordmark .dot{width:16px;height:16px;border-radius:50%;background:var(--teal)}

/* nav */
.site-nav{position:absolute;top:0;left:0;width:1200px;height:88px;display:flex;align-items:center;padding:0 80px;background:var(--white);border-bottom:1px solid var(--line)}
.site-nav .menu{margin-left:auto;display:flex;gap:34px;font-size:14px;font-weight:500;letter-spacing:.5px;color:var(--muted)}
.site-nav .menu .active{color:var(--teal)}
.site-nav .search{margin-left:36px;width:180px;height:34px;border:1px solid var(--line);border-radius:3px;font-size:13px;color:#aaa;display:flex;align-items:center;padding:0 12px;justify-content:space-between}

/* hero */
.hero{position:absolute;top:88px;left:0;width:1200px;height:632px;background:linear-gradient(180deg,#7fb3da 0%,#a9c9df 35%,#5f8fae 62%,#2d6a8e 100%)}
.hero .headline{position:absolute;top:52px;left:0;width:100%;text-align:center}
.hero h1{display:inline-block;background:rgba(29,111,174,.85);color:var(--white);font-size:48px;font-weight:400;padding:4px 20px}
.hero .tagline{display:inline-block;margin-top:8px;background:rgba(29,111,174,.85);color:var(--white);font-size:22px;font-weight:300;padding:4px 14px}
.hero .dots{position:absolute;bottom:24px;left:0;width:100%;display:flex;justify-content:center;gap:10px}
.hero .dots span{width:10px;height:10px;border-radius:50%;background:rgba(255,255,255,.5)}
.hero .dots span.on{background:var(--white)}

/* intro */
.intro{position:absolute;top:720px;left:0;width:1200px;height:492px;text-align:center}
.intro .wordmark{position:absolute;top:52px;left:0;width:100%;justify-content:center}
.intro .lead{position:absolute;top:112px;left:330px;width:540px;font-size:15px;line-height:1.5;color:var(--ink)}
.pillars{position:absolute;top:190px;left:190px;width:820px;display:flex;justify-content:space-between}
.pillar{width:240px}
.pillar svg{display:block;margin:0 auto 12px}
.pillar h3{font-size:16px;font-weight:700;color:var(--ink);margin-bottom:10px}
.pillar p{font-size:12px;line-height:1.5;color:var(--muted);text-align:left}
.pillar .more{display:block;margin-top:8px;font-size:12px;font-weight:700;color:var(--ink)}

/* oxidation band */
.oxidation{position:absolute;top:1212px;left:0;width:1200px;height:328px;background:linear-gradient(135deg,var(--blue) 0%,var(--blue-deep) 100%);color:var(--white);text-align:center}
.oxidation h2{margin-top:56px;font-size:28px;font-weight:400;letter-spacing:1px}
.oxidation .rule{width:60px;height:2px;background:var(--white);margin:14px auto 16px}
.oxidation p{width:700px;margin:0 auto;font-size:14px;line-height:1.6;font-weight:300}
.oxidation .points{display:flex;justify-content:center;gap:60px;margin:8px 0;font-size:14px}
.btn{display:inline-block;font-size:12px;font-weight:700;letter-spacing:.5px;padding:9px 20px;border-radius:2px}
.btn-light{background:var(--white);color:var(--ink)}
.btn-teal{background:var(--teal);color:var(--white)}
.oxidation .btn{margin-top:20px}

/* solutions */
.solutions-head{position:absolute;top:1540px;left:0;width:1200px;height:160px;text-align:center}
.solutions-head h2{margin-top:78px;font-size:28px;font-weight:700;color:var(--blue);letter-spacing:1px}
.solutions-head p{margin-top:10px;font-size:13px;color:var(--muted)}
.solution{position:absolute;left:0;width:1200px;height:280px;display:flex}
.solution .copy{width:600px;padding:36px 70px}
.solution .photo{width:600px;height:280px}
.solution h3{font-size:20px;font-weight:700;color:var(--ink);margin-bottom:14px}
.solution p{font-size:13px;line-height:1.6;color:var(--muted)}
.solution .btn{margin-top:18px}
.solution.flip .copy{text-align:right}
.fuel{top:1700px}
.voc{top:1980px}
.flue{top:2260px}
.water{top:2540px}

/* partners */
.partners{position:absolute;top:2820px;left:0;width:1200px;height:260px;display:flex;padding:40px 70px 0}
.partners .intro-col{width:280px}
.partners h3{font-size:20px;font-weight:700;margin-bottom:14px}
.partners .intro-col p{font-size:12px;line-height:1.5;color:var(--muted)}
.partners .pager{display:flex;gap:8px;margin-top:12px}
.partners .pager span{width:22px;height:22px;border-radius:50%;background:var(--teal)}
.partners .pager span.off{background:#cfcfcf}
.partner-list{display:flex;gap:22px;margin-left:30px}
.partner{width:170px;text-align:left}
.partner .badge{width:170px;height:110px;border:1px solid var(--line);display:flex;align-items:center;justify-content:center}
.partner .badge span{width:64px;height:64px;border-radius:50%}
.partner p{font-size:12px;color:var(--muted);margin-top:10px;line-height:1.4}

/* about */
.about{position:absolute;top:3080px;left:0;width:1200px;height:300px;background:linear-gradient(135deg,var(--teal) 0%,var(--teal-dark) 100%);color:var(--white);text-align:center}
.about h2{margin-top:52px;font-size:28px;font-weight:400;letter-spacing:1px}
.about .rule{width:60px;height:2px;background:var(--white);margin:14px auto 18px}
.about p{width:900px;margin:0 auto;font-size:13px;line-height:1.6}
.about .btn{margin-top:22px}

/* footer */
.contact{position:absolute;top:3380px;left:0;width:1200px;height:472px;background:var(--footer);color:#d6d6d6}
.contact h2{text-align:center;margin-top:48px;font-size:26px;color:var(--white);font-weight:400}
.contact .sub{text-align:center;width:520px;margin:12px auto 0;font-size:14px;line-height:1.5}
.contact .cols{position:absolute;top:180px;left:70px;width:1060px;display:flex}
.contact h4{color:var(--white);font-size:18px;font-weight:700;margin-bottom:18px}
.quick{width:240px}
.quick li{list-style:none;font-size:13px;line-height:2.1}
.reach{width:300px;font-size:13px;line-height:1.7}
.reach .row{display:flex;gap:10px;align-items:center;margin-top:10px}
.form{margin-left:auto;width:490px;display:grid;grid-template-columns:1fr 1fr;gap:10px}
.form .field{height:36px;border:1px solid #5a5c5e;font-size:12px;color:#9a9a9a;padding:10px 12px}
.form .field.wide{grid-column:1/3;height:90px}
.form .send{grid-column:1/2;justify-self:start;border:1px solid #8a8a8a;color:var(--white);font-size:12px;padding:9px 18px}
.bottom-bar{position:absolute;top:3852px;left:0;width:1200px;height:52px;background:var(--footer-deep);display:flex;align-items:center;padding:0 70px;font-size:12px;color:#9a9a9a}
.bottom-bar .social{margin-left:auto;display:flex;gap:8px}
.bottom-bar .social span{width:24px;height:24px;border-radius:50%;border:1px solid #8a8a8a}
</style>
</head>
<body>

<header class="site-nav">
  <div class="wordmark"><span class="dot"></span>Velqua</div>
  <nav class="menu">
    <a class="active">HOME</a><a>TECHNOLOGY</a><a>PRODUCTS</a><a>CONTACT</a>
  </nav>
  <div class="search">Search <span>&#9906;</span></div>
</header>

<section class="hero" role="img" aria-label="Photograph of a clean city skyline with towers reflected in a river">
  <div class="headline">
    <h1>New Ideas For A Cleaner World</h1><br>
    <span class="tagline">Advanced Oxidation Science for Environmental Pollution Management</span>
  </div>
  <div class="dots"><span class="on"></span><span></span></div>
</section>

<section class="intro">
  <div class="wordmark"><span class="dot"></span>Velqua Sciences</div>
  <p class="lead">Environmental pollution control solutions employing nature's most reactive Free Radical</p>
  <div class="pillars">
    <div class="pillar">
      <svg width="84" height="84" viewBox="0 0 84 84"><circle cx="42" cy="42" r="38" fill="none" stroke="#1d6fae" stroke-width="4" stroke-dasharray="200 40"/><path d="M42 22 C50 34 56 42 56 50 A14 14 0 0 1 28 50 C28 42 34 34 42 22Z" fill="#25b5ad"/></svg>
      <h3>WATER</h3>
      <p>Lorem ipsum dolor sit amet, consectetur adipiscing elit, sed do eiusmod tempor incididunt ut labore et dolore magna aliqua.</p>
      <span class="more">read more</span>
    </div>
    <div class="pillar">
      <svg width="84" height="84" viewBox="0 0 84 84"><circle cx="42" cy="42" r="38" fill="none" stroke="#1d6fae" stroke-width="4" stroke-dasharray="200 40"/><path d="M24 52 A9 9 0 0 1 28 35 A13 13 0 0 1 53 32 A10 10 0 0 1 60 52Z" fill="#25b5ad"/></svg>
      <h3>AIR</h3>
      <p>Lorem ipsum dolor sit amet, consectetur adipiscing elit, sed do eiusmod tempor incididunt ut labore et dolore magna aliqua.</p>
      <span class="more">read more</span>
    </div>
    <div class="pillar">
      <svg width="84" height="84" viewBox="0 0 84 84"><circle cx="42" cy="42" r="38" fill="none" stroke="#1d6fae" stroke-width="4" stroke-dasharray="200 40"/><rect x="28" y="30" width="20" height="30" rx="2" fill="#25b5ad"/><path d="M48 36 L56 40 L56 56" fill="none" stroke="#25b5ad" stroke-width="3"/><rect x="31" y="33" width="14" height="8" fill="#ffffff"/></svg>
      <h3>FUEL</h3>
      <p>Lorem ipsum dolor sit amet, consectetur adipiscing elit, sed do eiusmod tempor incididunt ut labore et dolore magna aliqua.</p>
      <span class="more">read more</span>
    </div>
  </div>
</section>

<section class="oxidation">
  <h2>ADVANCED OXIDATION</h2>
  <div class="rule"></div>
  <p>Advanced Oxidation refers to a variety of techniques employing the Hydroxyl Radical, an energetic, highly reactive cousin of the water molecule.</p>
  <div class="points"><span>&#10003; To add oxygen to inorganic molecules</span><span>&#10003; To remove hydrogen from organic molecules</span></div>
  <p>These transformations convert injurious industrial contaminants into reactive forms that can be captured or that disintegrate into harmless end products.</p>
  <span class="btn btn-light">LEARN MORE</span>
</section>

<section class="solutions-head">
  <h2>SOLUTIONS</h2>
  <p>Lorem ipsum dolor sit amet, consectetur adipiscing elit, sed do eiusmod tempor incididunt ut labore et dolore magna aliqua.</p>
</section>

<article class="solution fuel">
  <div class="copy">
    <h3>FUEL OIL DESULFURIZATION</h3>
    <p>Our proprietary low temperature and pressure advanced oxidation catalytic process reliably removes sulfur from diesel transportation fuel at less than half the operating costs of older hydro-desulfurization processes.</p>
    <span class="btn btn-teal">LEARN MORE</span>
  </div>
  <div class="photo" role="img" aria-label="Photograph of an illuminated refinery at dusk" style="background:linear-gradient(180deg,#3d4f7a 0%,#8a6a7a 45%,#c98a4a 70%,#3a3f55 100%)"></div>
</article>

<article class="solution voc flip">
  <div class="photo" role="img" aria-label="Photograph of a technician in protective suit handling chemical drums" style="background:linear-gradient(135deg,#5e6670 0%,#a9b0b6 45%,#d6d43a 60%,#4e565e 100%)"></div>
  <div class="copy">
    <h3>VOLATILE ORGANIC COMPUNDS (VOC)</h3>
    <p>Alkanes, alkenes, halogenated hydrocarbons, aromatic hydrocarbons, esters, aldehydes, polycyclic aromatic hydrocarbons. We convert these byproducts of industrial processes before they enter the atmosphere and cause smog.</p>
    <span class="btn btn-teal">LEARN MORE</span>
  </div>
</article>

<article class="solution flue">
  <div class="copy">
    <h3>FLUE GAS SCRUBBING</h3>
    <p>Desulfurization and denitrification using our proprietary flue gas advanced oxidation catalytic process (FGAO). Sulfur and nitrogen are oxidized and adsorbed into an environmentally friendly solid medium for safe removal from site.</p>
    <span class="btn btn-teal">LEARN MORE</span>
  </div>
  <div class="photo" role="img" aria-label="Photograph of a red and white industrial chimney against a blue sky" style="background:linear-gradient(180deg,#6fa6d6 0%,#a8cbe8 55%,#e4eef6 100%)"></div>
</article>

<article class="solution water flip">
  <div class="photo" role="img" aria-label="Photograph of a wastewater treatment channel" style="background:linear-gradient(135deg,#5a4a3a 0%,#8c7a62 40%,#b9a788 60%,#4a3e32 100%)"></div>
  <div class="copy">
    <h3>WASTEWATER TREATMENT</h3>
    <p>Photoelectrocatalysis (PEC) anodic oxidation removes soluble organics. Novel anode design using our proprietary nano-carbon surface operates cost-effectively to remove 99% of contaminants across a wide range of chemical oxygen demand.</p>
    <span class="btn btn-teal">LEARN MORE</span>
  </div>
</article>

<section class="partners">
  <div class="intro-col">
    <h3>PARTNERS</h3>
    <p>Lorem ipsum dolor sit amet, consectetur adipiscing elit, sed do eiusmod tempor incididunt ut labore et dolore magna aliqua.</p>
    <div class="pager"><span></span><span class="off"></span></div>
  </div>
  <div class="partner-list">
    <div class="partner"><div class="badge"><span style="background:#2a8fd0"></span></div><p>Our sales partner in China</p></div>
    <div class="partner"><div class="badge"><span style="background:#d84a2a"></span></div><p>Our construction partner in China</p></div>
    <div class="partner"><div class="badge"><span style="background:#3a78b8"></span></div><p>Our technology partner in China</p></div>
    <div class="partner"><div class="badge"><span style="background:#b83a3a"></span></div><p>Our technology partner in China</p></div>
  </div>
</section>

<section class="about">
  <h2>ABOUT VELQUA SCIENCES</h2>
  <div class="rule"></div>
  <p>Lorem ipsum dolor sit amet, consectetur adipiscing elit, sed do eiusmod tempor incididunt ut labore et dolore magna aliqua. Ut enim ad minim veniam, quis nostrud exercitation ullamco laboris nisi ut aliquip ex ea commodo consequat. Duis aute irure dolor in reprehenderit in voluptate velit esse cillum dolore eu fugiat nulla pariatur. Excepteur sint occaecat cupidatat non proident, sunt in culpa qui officia.</p>
  <span class="btn btn-light">LEARN MORE</span>
</section>

<footer class="contact">
  <h2>CONTACT</h2>
  <p class="sub">We welcome inquiries regarding the licensing, distribution, and purchase of our products, systems, and technologies.</p>
  <div class="cols">
    <div class="quick">
      <h4>Quick Links</h4>
      <ul><li>Home</li><li>About</li><li>Services</li><li>Our Team</li><li>Links</li><li>Contact</li></ul>
    </div>
    <div class="reach">
      <h4>Contact Us</h4>
      <div class="row"><svg width="14" height="18" viewBox="0 0 14 18"><path d="M7 0a7 7 0 0 1 7 7c0 5-7 11-7 11S0 12 0 7a7 7 0 0 1 7-7z" fill="#d6d6d6"/><circle cx="7" cy="7" r="2.5" fill="#2f3133"/></svg><span>Velqua Science Corp.<br>Harbor District, Examplestate</span></div>
      <div class="row"><svg width="16" height="16" viewBox="0 0 16 16"><path d="M3 1l3 3-2 2c1 2 3 4 5 5l2-2 3 3-2 3C6 14 2 10 1 3z" fill="#d6d6d6"/></svg><span>Help: +1 555 0142 7788</span></div>
      <div class="row"><svg width="16" height="12" viewBox="0 0 16 12"><rect x="0.5" y="0.5" width="15" height="11" fill="none" stroke="#d6d6d6"/><path d="M1 1l7 6 7-6" fill="none" stroke="#d6d6d6"/></svg><span>info@velquaresearch.example</span></div>
    </div>
    <div class="form">
      <div class="field">Name</div><div class="field">Email</div>
      <div class="field">Phone</div><div class="field">Subject</div>
      <div class="field wide">Message</div>
      <div class="send">SEND MESSAGE</div>
    </div>
  </div>
</footer>
<div class="bottom-bar">
  <span>Copyright © 2016 Velqua Sciences. All rights reserved.</span>
  <div class="social"><span></span><span></span><span></span><span></span></div>
</div>

</body>
</html>
```